Business Card Design Can you design a business card design? Looking for something unique and differe

Can you design a business card design? Looking for something unique and different. Can you design a business card design? Looking for something unique and different.Can you design a business card design? Looking for something unique and different.Can you design a business card design? Looking for something unique and different.Can you design a business card design? Looking for something unique and different.Can you design a business card design? Looking for something unique and different.

Industry/Entity Type

Business

Contact Information for Business Card

Can you design a business card design? Looking for something unique and different.

Font styles to use
Serif

```html
<!DOCTYPE html>
<html lang="en">
<head>
<meta charset="utf-8">
<title>Meridian Business Card</title>
<link rel="stylesheet" href="https://fonts.googleapis.com/css2?family=Open+Sans:wght@400;600;700&display=swap">
<style>
  :root {
    --backdrop: #7d7d7d;
    --card: #ffffff;
    --card-shade: #f3f3f3;
    --purple: #9d7fad;
    --purple-text: #9a75b0;
    --ink: #2d2d2d;
    --muted: #555555;
    --rule: #b9b9b9;
  }
  * { box-sizing: border-box; margin: 0; padding: 0; }
  html, body { width: 1200px; height: 900px; overflow: hidden; }
  body {
    background: var(--backdrop);
    font-family: "Open Sans", Arial, sans-serif;
    display: flex;
    align-items: center;
    justify-content: center;
    gap: 60px;
  }
  .card {
    position: relative;
    width: 525px;
    height: 300px;
    background: linear-gradient(180deg, var(--card) 0%, var(--card-shade) 100%);
    box-shadow: 0 10px 24px rgba(0,0,0,0.25);
    overflow: hidden;
  }
  /* Front: contact side */
  .contact { position: absolute; left: 34px; top: 30px; }
  .contact__name { color: var(--purple-text); font-weight: 700; font-size: 21px; line-height: 1.1; }
  .contact__role { color: var(--muted); font-size: 12px; margin-top: 2px; }
  .contact__list { margin-top: 24px; list-style: none; }
  .contact__label { color: var(--purple-text); font-size: 11px; line-height: 1.2; }
  .contact__value { color: var(--ink); font-size: 13px; line-height: 1.25; margin-bottom: 3px; }
  .brand {
    position: absolute;
    display: flex;
    align-items: center;
    gap: 10px;
  }
  .brand__square { width: 26px; height: 26px; background: var(--purple); }
  .brand__name {
    color: var(--purple-text);
    font-weight: 700;
    font-size: 30px;
    letter-spacing: 0.5px;
    padding-bottom: 6px;
    border-bottom: 1px solid var(--rule);
  }
  .card--front .brand { right: 36px; bottom: 62px; }
  /* Back: brand side */
  .card--back .panel { position: absolute; inset: 0; }
  .card--back .brand { right: 40px; top: 130px; }
</style>
</head>
<body>
  <section class="card card--front">
    <div class="contact">
      <p class="contact__name">Daniel Archer</p>
      <p class="contact__role">Managing Director</p>
      <ul class="contact__list">
        <li><p class="contact__label">telephone</p><p class="contact__value">044-987 654 321</p></li>
        <li><p class="contact__label">email</p><p class="contact__value">hello@meridiancm.com</p></li>
        <li><p class="contact__label">address</p><p class="contact__value">18 Harbour Lane, Leeds, UK</p></li>
      </ul>
    </div>
    <div class="brand">
      <span class="brand__square"></span>
      <span class="brand__name">Meridian</span>
    </div>
  </section>

  <section class="card card--back">
    <svg class="panel" width="525" height="300" viewBox="0 0 525 300" aria-hidden="true">
      <polygon points="0,0 275,0 220,300 0,300" fill="var(--purple)"/>
    </svg>
    <div class="brand">
      <span class="brand__square"></span>
      <span class="brand__name">Meridian</span>
    </div>
  </section>
</body>
</html>
```